QP Fiduciary Website Redesign Contest

We want to refresh our website to be more insitutional, professional for an international audience. We have designed a new logo for this purpose and that has been attached. A full brand brief and positioning statement has also been attached. Please read through all the documents carefully before designing. The old website is found here: https://qp-fiduciary.example/

Target Market(s)

Actuaries and associated businesses internationally

Industry/Entity Type

professional services - actuaries

Number of Pages Required

3 page

Font styles to use
Sans Serif

Colors
0054AA
0677BA
7BADD7
CADEEF
E8F1F8
0094D4
00A9DD
6FCCEA
C7EBF8
E9F6FB
F0912C
F2A743
F7CA91
FBE8D2
FDF5EE
EE7325
F08F49
F5BC92
FAE3D3
FDF4ED
EB3D1F
EC4F4E
F09395
F8D3D4
FCEDEE

Requirements
Must have
• blues and greens to match the logo color, complimentary colors, navigation
Nice to have
• old site: https://qp-fiduciary.example/

```html
<!DOCTYPE html>
<html lang="en">
<head>
<meta charset="utf-8">
<title>QP Fiduciary — Actuarial Software</title>
<link rel="stylesheet" href="https://fonts.googleapis.com/css2?family=Montserrat:wght@400;500;600;700;800&family=Open+Sans:wght@400;600&display=swap">
<style>
:root{
  --stage:#e3e3e3;
  --white:#ffffff;
  --ink:#1d1d1f;
  --muted:#5b5b60;
  --red:#eb3d1f;
  --red-deep:#c8200f;
  --orange:#ee7325;
  --orange-soft:#fae3d3;
  --grey-band:#f2f2f2;
  --card-line:#e4e4e4;
  --black:#0b0b0b;
  --footer-text:#bdbdbd;
}
*{box-sizing:border-box;margin:0;padding:0}
html,body{width:1200px;height:2300px;overflow:hidden}
body{background:var(--stage);font-family:"Open Sans",Arial,sans-serif;color:var(--ink)}
.page{position:absolute;left:88px;top:40px;width:1024px;height:2220px;background:var(--white);box-shadow:0 4px 18px rgba(0,0,0,.12);overflow:hidden}
h1,h2,h3,.brand,.nav a,.btn{font-family:"Montserrat",Arial,sans-serif}

/* header */
.site-header{height:72px;display:flex;align-items:center;justify-content:space-between;padding:0 28px}
.brand{font-weight:800;font-size:22px;color:var(--red);letter-spacing:.5px;display:flex;align-items:center;gap:8px}
.brand-dot{width:12px;height:12px;background:var(--red);border-radius:50%}
.nav{display:flex;align-items:center;gap:22px}
.nav a{font-size:12px;font-weight:500;color:var(--ink);text-decoration:none}
.nav a.active{color:var(--red)}
.btn{display:inline-block;font-weight:700;text-decoration:none;color:var(--white);background:var(--red);font-size:11px;padding:9px 14px;border-radius:2px}

/* hero */
.hero{height:408px;background:radial-gradient(ellipse at 75% 20%,#f04a2c 0%,var(--red) 40%,var(--red-deep) 100%);color:var(--white);text-align:center;display:flex;flex-direction:column;align-items:center;justify-content:center;padding:0 180px}
.hero h1{font-size:40px;font-weight:700;line-height:1.15;margin-bottom:18px}
.hero p{font-size:16px;line-height:1.5;margin-bottom:26px;opacity:.95}
.hero .btn{background:var(--white);color:var(--red);font-size:13px;padding:13px 22px}

/* overview */
.overview{height:352px;background:var(--orange);color:var(--white);text-align:center;display:flex;flex-direction:column;align-items:center;justify-content:center;padding:0 110px}
.section-title{font-size:40px;font-weight:800;letter-spacing:.5px;margin-bottom:24px}
.overview p{font-size:14px;line-height:1.6;margin-bottom:22px}
.overview .btn{background:var(--red);font-size:12px;padding:9px 16px}
.accent{color:var(--red)}

/* solutions */
.solutions{height:468px;background:var(--grey-band);text-align:center;padding-top:70px}
.solutions .section-title,.traits .section-title{color:var(--ink)}
.cards{display:flex;justify-content:center;gap:30px;margin-top:10px}
.card{width:276px;height:214px;background:var(--white);border:1px solid var(--card-line);border-radius:4px;padding:28px 24px;text-align:center;box-shadow:0 2px 8px rgba(0,0,0,.05)}
.card svg{width:34px;height:34px;margin-bottom:10px}
.card h3{font-size:16px;font-weight:700;margin-bottom:10px}
.card p{font-size:12px;line-height:1.55;color:var(--muted);margin-bottom:14px}
.learn{font-family:"Montserrat",Arial,sans-serif;font-size:11px;font-weight:700;color:var(--red);text-decoration:none}

/* traits */
.traits{height:520px;background:var(--white);padding-top:70px;text-align:center}
.trait-grid{display:grid;grid-template-columns:1fr 1fr;column-gap:80px;row-gap:44px;width:720px;margin:20px auto 0;text-align:left}
.trait{display:flex;gap:16px;align-items:flex-start}
.trait-icon{flex:0 0 44px;height:44px;border-radius:50%;background:var(--orange-soft);display:flex;align-items:center;justify-content:center}
.trait-icon svg{width:24px;height:24px}
.trait h3{font-size:16px;font-weight:700;margin-bottom:6px}
.trait p{font-size:12px;line-height:1.55;color:var(--muted)}

/* cta */
.cta{height:280px;background:var(--red);color:var(--white);text-align:center;display:flex;flex-direction:column;align-items:center;justify-content:center}
.cta .section-title{color:var(--white);font-size:38px;margin-bottom:26px}
.cta .btn{background:var(--black);font-size:14px;padding:14px 26px}

/* footer */
.site-footer{height:120px;background:var(--black);color:var(--footer-text);padding:22px 60px 0}
.footer-cols{display:flex;justify-content:space-between;width:820px}
.footer-col h4{font-family:"Montserrat",Arial,sans-serif;font-size:10px;font-weight:700;color:var(--white);margin-bottom:6px}
.footer-col li{list-style:none;font-size:8px;line-height:1.6}
.copyright{text-align:center;font-size:7px;margin-top:14px;color:#8a8a8a}
</style>
</head>
<body>
<div class="page">
  <header class="site-header">
    <div class="brand"><span class="brand-dot"></span>QP FIDUCIARY</div>
    <nav class="nav">
      <a class="active" href="#">Home</a>
      <a href="#">Platform</a>
      <a href="#">Solutions</a>
      <a href="#">Insights</a>
      <a href="#">Company</a>
      <a href="#">Contact</a>
      <a class="btn" href="#">Request a Technical Walkthrough</a>
    </nav>
  </header>

  <section class="hero" role="img" aria-label="Red banner with soft abstract flowing line texture">
    <h1>Actuarial software for structured, auditable financial analysis</h1>
    <p>Software that translates actuarial methodologies into disciplined decision-ready analytical tools across diverse regulatory environments.</p>
    <a class="btn" href="#">Request a Technical Walkthrough</a>
  </section>

  <section class="overview">
    <h2 class="section-title">PLATFORM OVERVIEW</h2>
    <p>QP Fiduciary develops modular actuarial software designed to support reserving, valuation, pricing and enterprise risk management workflows across diverse regulatory environments. Our platforms translate established actuarial methodologies into disciplined, audit-ready tools, ensuring transparency and governance at every step.</p>
    <a class="btn" href="#">EXPLORE PLATFORM</a>
  </section>

  <section class="solutions">
    <h2 class="section-title">CORE <span class="accent">SOLUTIONS</span></h2>
    <div class="cards">
      <article class="card">
        <svg viewBox="0 0 24 24" fill="none" stroke="#eb3d1f" stroke-width="1.6"><rect x="4" y="3" width="16" height="18" rx="2"/><path d="M8 8h8M8 12h8M8 16h5"/></svg>
        <h3>Reserving &amp; Valuation</h3>
        <p>Structured workflows and financial reporting across jurisdictions built on disciplined actuarial methodologies.</p>
        <a class="learn" href="#">LEARN MORE →</a>
      </article>
      <article class="card">
        <svg viewBox="0 0 24 24" fill="none" stroke="#eb3d1f" stroke-width="1.6"><circle cx="12" cy="12" r="9"/><path d="M14.5 9c-.5-1-1.5-1.5-2.5-1.5-1.5 0-2.5.8-2.5 2s1 1.7 2.5 2 2.5.8 2.5 2-1 2-2.5 2c-1 0-2-.5-2.5-1.5M12 6v1.5M12 16.5V18"/></svg>
        <h3>Pricing</h3>
        <p>Insurance and reinsurance pricing models grounded in transparency, enabling accurate, sustainable decisions.</p>
        <a class="learn" href="#">LEARN MORE →</a>
      </article>
      <article class="card">
        <svg viewBox="0 0 24 24" fill="none" stroke="#eb3d1f" stroke-width="1.6"><path d="M12 3l8 3v6c0 5-3.5 8-8 9-4.5-1-8-4-8-9V6z"/><path d="M8.5 12l2.5 2.5 4.5-5"/></svg>
        <h3>Enterprise Risk Management</h3>
        <p>Tools supporting risk appetite definition and capital modeling for comprehensive enterprise risk management.</p>
        <a class="learn" href="#">LEARN MORE →</a>
      </article>
    </div>
  </section>

  <section class="traits">
    <h2 class="section-title">PLATFORM <span class="accent">CHARACTERISTICS</span></h2>
    <div class="trait-grid">
      <div class="trait">
        <div class="trait-icon"><svg viewBox="0 0 24 24" fill="none" stroke="#ee7325" stroke-width="1.8"><path d="M4 6h16M4 12h16M4 18h10"/></svg></div>
        <div><h3>Structured Workflows</h3><p>Disciplined processes built to support multi-stakeholder review and actuarial governance.</p></div>
      </div>
      <div class="trait">
        <div class="trait-icon"><svg viewBox="0 0 24 24" fill="none" stroke="#ee7325" stroke-width="1.8"><path d="M2 12s4-7 10-7 10 7 10 7-4 7-10 7S2 12 2 12z"/><circle cx="12" cy="12" r="3"/></svg></div>
        <div><h3>Transparent Assumptions</h3><p>Clear documentation of assumptions and methodology for auditability and defensibility.</p></div>
      </div>
      <div class="trait">
        <div class="trait-icon"><svg viewBox="0 0 24 24" fill="none" stroke="#ee7325" stroke-width="1.8"><path d="M4 20V10M10 20V4M16 20v-7M22 20H2"/></svg></div>
        <div><h3>Comparative Analysis</h3><p>Capabilities for scenario comparison and sensitivity analysis to inform professional judgment.</p></div>
      </div>
      <div class="trait">
        <div class="trait-icon"><svg viewBox="0 0 24 24" fill="none" stroke="#ee7325" stroke-width="1.8"><path d="M12 3l8 3v6c0 5-3.5 8-8 9-4.5-1-8-4-8-9V6z"/><path d="M8.5 12l2.5 2.5 4.5-5"/></svg></div>
        <div><h3>Governance Ready</h3><p>Outputs designed to support regulator and board review, ensuring compliance and clarity.</p></div>
      </div>
    </div>
  </section>

  <section class="cta">
    <h2 class="section-title">INTERESTED IN EXPLORING THE PLATFORM?</h2>
    <a class="btn" href="#">Request a Technical Walkthrough</a>
  </section>

  <footer class="site-footer">
    <div class="footer-cols">
      <div class="footer-col"><h4>Company</h4><ul><li>About</li><li>Careers</li><li>News</li></ul></div>
      <div class="footer-col"><h4>Platform</h4><ul><li>Overview</li><li>Reserving &amp; Valuation</li><li>Pricing</li><li>Enterprise Risk Management</li></ul></div>
      <div class="footer-col"><h4>Insights</h4><ul><li>Articles</li><li>Guides</li><li>Events</li></ul></div>
      <div class="footer-col"><h4>Contact</h4><ul><li>Email us</li><li>Request a Walkthrough</li></ul></div>
    </div>
    <p class="copyright">© QP Fiduciary. All rights reserved.</p>
  </footer>
</div>
</body>
</html>
```